New design for Comparison website

We need new design for our website https://prisvaktposten.no/ . We compare prices and providers in different niches such as electricity, mobile plans, broadband etc.

We would like to see design like Tarivo com or our competitor kjøpklokt no

We will need design of all pages, with tables, tables are somewhat different depending on the service compared (use kjøpklokt no for reference) . Our focus is CTR through comparison Tables.

Final design must communicate following: Professionalism, thrust, authority.

Number of Pages Required

5+ page

Font styles to use
Sans Serif

Colors

Designer to choose colors to be used in the design.

Requirements
Must have
• Tables
Nice to have
• Images in content

```html
<!DOCTYPE html>
<html lang="en">
<head>
<meta charset="utf-8">
<title>Prisvaktposten – Compare providers</title>
<link rel="stylesheet" href="https://fonts.googleapis.com/css2?family=Roboto+Condensed:wght@400;700&family=Open+Sans:wght@400;600;700&display=swap">
<style>
:root{
  --green:#13a07a;
  --green-dark:#0c8a68;
  --orange:#f28c1c;
  --ink:#2b2b2b;
  --muted:#555;
  --line:#e2e2e2;
  --footer:#1d1d1d;
  --footer-line:#333;
  --white:#fff;
}
*{box-sizing:border-box;margin:0;padding:0}
html,body{width:1200px;height:3291px;overflow:hidden}
body{position:relative;background:var(--white);font-family:"Open Sans",Arial,sans-serif;color:var(--ink)}
.abs{position:absolute}
.heading{font-family:"Roboto Condensed",Arial,sans-serif;font-weight:700;text-transform:uppercase}

/* top bar */
.topbar{left:0;top:0;width:1200px;height:60px;background:var(--green);color:var(--white);font-size:12px;font-weight:600}
.topbar .links{left:98px;top:21px}
.topbar .links span{margin:0 6px}
.topbar .contact{right:98px;top:21px;display:flex;gap:38px}
.topbar .contact div{display:flex;align-items:center;gap:8px}

/* header */
.header{left:0;top:60px;width:1200px;height:76px;background:var(--white)}
.brand{display:flex;align-items:center;gap:10px;font-family:"Roboto Condensed",Arial,sans-serif;font-weight:700;font-size:30px}
.header .brand{left:99px;top:20px;color:var(--green-dark)}
.brand .dot{width:30px;height:30px;border-radius:50%;background:currentColor}
.nav{right:98px;top:20px;display:flex;gap:8px;font-family:"Roboto Condensed",Arial,sans-serif;font-size:14px;text-transform:uppercase;color:#333}
.nav a{padding:8px 12px;border-radius:18px;text-decoration:none;color:inherit}
.nav a.active{border:2px solid var(--green);color:var(--green)}

/* hero */
.hero{left:0;top:136px;width:1200px;height:600px;background:linear-gradient(120deg,#6b5a45 0%,#3a3b3d 40%,#5a6168 70%,#2f3338 100%);overflow:hidden}
.hero .photo{position:absolute;inset:0}
.hero h1{position:absolute;top:170px;width:100%;text-align:center;color:var(--white);font-size:42px;letter-spacing:.5px}
.hero .lead{position:absolute;top:226px;width:100%;text-align:center;color:var(--white);font-size:16px}
.search{position:absolute;left:340px;top:274px;width:520px;height:38px;display:flex;border-radius:20px;overflow:hidden}
.search .field{flex:1;background:var(--white);font-size:12px;color:#666;padding:11px 18px}
.search .btn{width:100px;background:var(--green);color:var(--white);font-size:13px;font-weight:600;text-align:center;line-height:38px}
.hero .arrow{position:absolute;top:222px}
.hero .curve{position:absolute;left:0;bottom:0}

/* how it works */
.section-title{width:1200px;left:0;text-align:center;font-size:34px;color:var(--ink)}
.step{width:300px;text-align:center}
.step .pin{margin:0 auto}
.step h3{font-family:"Open Sans",sans-serif;font-weight:400;font-size:14px;text-transform:uppercase;margin-top:24px}
.step h4{font-weight:400;font-size:14px;margin-top:4px}
.step p{font-size:11.5px;line-height:20px;color:var(--muted);margin:10px auto 0;width:260px}

/* categories band */
.band{left:0;top:1125px;width:1200px;height:446px;background:linear-gradient(90deg,#3d4147 0%,#2b2e33 45%,#4b4f55 75%,#5d5f62 100%)}
.band .photo{left:0;top:0;width:600px;height:446px;background:radial-gradient(ellipse at 45% 45%,#7d8ea0 0%,#3b4652 45%,#23272c 100%)}
.band .content{left:610px;top:68px;width:540px;color:var(--white)}
.band h2{font-size:32px;line-height:44px;margin-top:26px}
.band p{font-size:11.5px;line-height:22px;margin-top:20px;color:#e8e8e8}
.outline-btn{display:inline-block;margin-top:24px;border:2px solid var(--white);border-radius:20px;padding:8px 24px;font-size:13px;font-family:"Roboto Condensed",sans-serif;text-transform:uppercase}

/* price cards */
.price-card{top:1779px;width:320px;height:349px;border:1px solid var(--line);background:var(--white)}
.price-card .photo{height:132px;display:flex;align-items:flex-end;justify-content:center;padding-bottom:16px;color:var(--white);font-family:"Roboto Condensed",sans-serif;font-size:25px}
.price-card .badge{position:absolute;left:98px;top:-73px;width:124px;height:124px;border-radius:50%;background:var(--green);border:5px solid var(--white);color:var(--white);text-align:center;font-family:"Roboto Condensed",sans-serif;font-weight:700;font-size:27px;line-height:30px;padding-top:28px}
.price-card ul{list-style:none}
.price-card li{height:37px;line-height:37px;border-bottom:1px solid var(--line);text-align:center;font-size:12px;color:var(--muted)}
.green-btn{display:inline-block;background:var(--green);color:var(--white);font-family:"Roboto Condensed",sans-serif;font-weight:700;font-size:15px;text-transform:uppercase;padding:7px 14px;border-radius:2px}
.price-card .cta{text-align:center;margin-top:16px}

/* why choose us */
.why{left:0;top:2211px;width:1200px;height:540px;background:linear-gradient(90deg,#3fae63 0%,#55b96e 35%,#3ab27e 65%,#5ec9a8 100%)}
.why .curve{position:absolute;left:0;bottom:0}
.why h2{position:absolute;top:62px;width:100%;text-align:center;color:var(--white);font-size:34px}
.feature{top:147px;width:239px;height:279px;background:var(--white)}
.feature .photo{height:158px}
.feature h3{font-weight:400;font-size:16px;text-align:center;margin-top:16px}
.feature p{font-size:11px;line-height:17px;color:var(--muted);text-align:center;margin:8px 18px 0}

/* newsletter strip */
.subscribe-icon{left:196px;top:2806px;width:52px;height:52px;border-radius:50%;background:var(--orange)}
.subscribe-text{left:270px;top:2810px}
.subscribe-text h3{font-family:"Roboto Condensed",sans-serif;font-weight:400;font-size:20px;text-transform:uppercase;color:#333}
.subscribe-text p{font-size:14px;color:#666;margin-top:2px}
.subscribe-form{left:564px;top:2810px;display:flex;height:46px}
.subscribe-form .field{width:311px;border:1px solid var(--line);font-size:12px;color:#666;padding:15px 12px}
.subscribe-form .btn{width:130px;background:var(--orange);color:var(--white);font-size:14px;text-align:center;line-height:46px;text-transform:uppercase}

/* footer */
.footer{left:0;top:2931px;width:1200px;height:360px;background:var(--footer);color:var(--white)}
.footer .brand{left:99px;top:84px;color:var(--white);font-size:28px}
.socials{left:101px;top:142px;display:flex;gap:6px}
.socials span{width:22px;height:22px;border-radius:50%;border:1.5px solid #bbb}
.footer h4{font-family:"Roboto Condensed",sans-serif;font-weight:400;font-size:18px;text-transform:uppercase}
.footer .col{top:52px;font-size:12.5px;line-height:22px;color:#ddd}
.footer .contact-col{left:384px;width:260px}
.contact-col .addr{margin-top:20px}
.contact-col .row{display:flex;align-items:center;gap:12px;margin-top:12px}
.links-col{left:671px}
.links-col ul{list-style:none;margin-top:18px}
.links-col li{font-size:11px;line-height:26px;display:flex;align-items:center;gap:12px}
.links-col li::before{content:"";width:7px;height:7px;border-radius:50%;background:#ddd}
.news-col{left:856px;width:245px}
.news-col p{font-size:11px;line-height:19px;margin-top:18px}
.news-col .field{margin-top:14px;background:var(--white);height:42px;color:#666;font-size:11px;padding:13px 12px}
.news-col .btn{display:inline-block;margin-top:14px;background:var(--green);color:var(--white);font-size:12px;font-weight:600;text-transform:uppercase;padding:7px 14px}
.footer .bottom{left:0;top:290px;width:1200px;border-top:1px solid var(--footer-line);text-align:center;font-size:11px;color:#ccc;padding-top:30px}
</style>
</head>
<body>

<div class="topbar abs">
  <div class="links abs">Home<span>|</span>About us<span>|</span>Contact<span>|</span>Terms<span>|</span>Privacy<span>|</span>Cookies</div>
  <div class="contact abs">
    <div><svg width="12" height="12" viewBox="0 0 24 24"><path fill="#fff" d="M6.6 10.8a15 15 0 0 0 6.6 6.6l2.2-2.2c.3-.3.7-.4 1-.2 1.1.4 2.3.6 3.6.6.6 0 1 .4 1 1V20c0 .6-.4 1-1 1A17 17 0 0 1 3 4c0-.6.4-1 1-1h3.5c.6 0 1 .4 1 1 0 1.3.2 2.5.6 3.6.1.3 0 .7-.2 1z"/></svg>Telephone: 912.555.0147</div>
    <div><svg width="13" height="11" viewBox="0 0 26 20"><rect x="1" y="1" width="24" height="18" fill="none" stroke="#fff" stroke-width="2"/><path d="M1 1l12 10L25 1" fill="none" stroke="#fff" stroke-width="2"/></svg>Email: info@prisvaktposten.no</div>
  </div>
</div>

<header class="header abs">
  <div class="brand abs"><span class="dot"></span>Prisvaktposten</div>
  <nav class="nav abs">
    <a class="active">Home</a><a>Broadband</a><a>MMS</a><a>Current</a><a>Hosting and Domains</a><a>Residential Alarm</a>
  </nav>
</header>

<section class="hero abs">
  <div class="photo" role="img" aria-label="People using smartphones and a laptop"></div>
  <h1 class="heading">Those who seek shall find</h1>
  <p class="lead">See if you use the best provider of services</p>
  <div class="search"><div class="field">Sed ut perspiciatis unde</div><div class="btn">SEARCH</div></div>
  <svg class="arrow" style="left:44px" width="30" height="60" viewBox="0 0 30 60"><path d="M26 2L4 30l22 28" fill="none" stroke="#fff" stroke-width="2"/></svg>
  <svg class="arrow" style="left:1126px" width="30" height="60" viewBox="0 0 30 60"><path d="M4 2l22 28L4 58" fill="none" stroke="#fff" stroke-width="2"/></svg>
  <svg class="curve" width="1200" height="120" viewBox="0 0 1200 120">
    <path d="M0 120 L0 70 Q600 -20 1200 70 L1200 120 Z" fill="#fff"/>
    <path d="M0 66 Q600 -26 1200 66" fill="none" stroke="#13a07a" stroke-width="5"/>
  </svg>
</section>

<h2 class="section-title heading abs" style="top:700px">How it works</h2>

<div class="step abs" style="left:80px;top:790px">
  <svg class="pin" width="106" height="120" viewBox="0 0 106 120"><path d="M53 0a53 53 0 0 1 14 104L53 120 39 104A53 53 0 0 1 53 0z" fill="#13a07a"/><path d="M40 30h20l10 10v36H40z" fill="#fff"/><path d="M46 48h18M46 56h18M46 64h18" stroke="#13a07a" stroke-width="3"/></svg>
  <h3>Select category</h3><h4>Read more about the service</h4>
  <p>We collect the most relevant information about the service in one place so that you learn the most important thing in a short time.</p>
</div>
<div class="step abs" style="left:460px;top:790px">
  <svg class="pin" width="106" height="120" viewBox="0 0 106 120"><path d="M53 0a53 53 0 0 1 14 104L53 120 39 104A53 53 0 0 1 53 0z" fill="#13a07a"/><path d="M50 32a22 22 0 1 0 22 22H50z" fill="#fff"/><path d="M56 27v21h21a21 21 0 0 0-21-21z" fill="#fff"/></svg>
  <h3>Compare providers</h3><h4>Choose among the best &amp; most reliable.</h4>
  <p>The best and most reputable players compared so you can choose the one that suits you best.</p>
</div>
<div class="step abs" style="left:811px;top:790px">
  <svg class="pin" width="106" height="120" viewBox="0 0 106 120"><path d="M53 0a53 53 0 0 1 14 104L53 120 39 104A53 53 0 0 1 53 0z" fill="#13a07a"/><path d="M30 34h8l6 26h26l5-18H41" fill="none" stroke="#fff" stroke-width="5" stroke-linejoin="round"/><circle cx="47" cy="70" r="4" fill="#fff"/><circle cx="67" cy="70" r="4" fill="#fff"/></svg>
  <h3>Order service</h3><h4>Order the best supplier</h4>
  <p>Order the service and enjoy that you've got the best provider quickly and easily.</p>
</div>
<svg class="abs" style="left:392px;top:838px" width="76" height="24" viewBox="0 0 76 24"><path d="M2 20Q36 -4 70 12" fill="none" stroke="#333" stroke-width="2" stroke-dasharray="4 4"/><path d="M62 6l9 7-10 4" fill="none" stroke="#333" stroke-width="2"/></svg>
<svg class="abs" style="left:760px;top:852px" width="76" height="24" viewBox="0 0 76 24"><path d="M2 4Q36 28 70 10" fill="none" stroke="#333" stroke-width="2" stroke-dasharray="4 4"/><path d="M62 4l9 5-8 7" fill="none" stroke="#333" stroke-width="2"/></svg>

<section class="band abs">
  <div class="photo abs" role="img" aria-label="Hand holding a tablet with a cloud network graphic"></div>
  <div class="content abs">
    <div class="brand" style="color:#fff;font-size:0"><span class="dot" style="width:38px;height:38px"></span></div>
    <h2 class="heading">Look through the available<br>categories</h2>
    <p>Begin to investigate and compare the providers of the services you need.. totam rem aperiam, eaque ipsa quae ab illo inventore veritatis et quasi architecto beatae vitae dicta sunt explicabo. Nemo enim ipsam voluptatem quia voluptas sit aspernatur aut odit aut fugit</p>
    <span class="outline-btn">Read more</span>
  </div>
</section>

<h2 class="section-title heading abs" style="top:1628px">Compare prices</h2>

<div class="price-card abs" style="left:99px">
  <div class="photo" role="img" aria-label="Electricity pylons at dusk" style="background:linear-gradient(180deg,#5d6670,#2f363d)">Electricity</div>
  <div class="badge">$6.00<br>Month</div>
  <ul><li>Sed ut perspiciatis unde omnis</li><li>Nemo enim ipsam voluptatem</li><li>Ut enim ad minima veniam</li><li>Lorem ipsum dolor</li></ul>
  <div class="cta"><span class="green-btn">Get started</span></div>
</div>
<div class="price-card abs" style="left:439px">
  <div class="photo" role="img" aria-label="Person holding a mobile phone" style="background:linear-gradient(180deg,#8a7a62,#3e3a35)">Mobile Plans</div>
  <div class="badge">$6.00<br>Month</div>
  <ul><li>Sed ut perspiciatis unde omnis</li><li>Nemo enim ipsam voluptatem</li><li>Ut enim ad minima veniam</li><li>Lorem ipsum dolor</li></ul>
  <div class="cta"><span class="green-btn">Get started</span></div>
</div>
<div class="price-card abs" style="left:781px">
  <div class="photo" role="img" aria-label="City skyline with network lights" style="background:linear-gradient(180deg,#4b5866,#222a33)">Broadband</div>
  <div class="badge">$6.00<br>Month</div>
  <ul><li>Sed ut perspiciatis unde omnis</li><li>Nemo enim ipsam voluptatem</li><li>Ut enim ad minima veniam</li><li>Lorem ipsum dolor</li></ul>
  <div class="cta"><span class="green-btn">Get started</span></div>
</div>

<section class="why abs">
  <h2 class="heading">Why choose us?</h2>
  <div class="feature abs" style="left:99px">
    <div class="photo" role="img" aria-label="Laptop on a desk showing a domain page" style="background:linear-gradient(135deg,#d8a067,#6f8fa5)"></div>
    <h3>Cheap Domain</h3><p>Mauris vel lacus vitae felis vestibulum volutpat imperdiet ac nisl Cum sociis natoque sodales velit</p>
  </div>
  <div class="feature abs" style="left:353px">
    <div class="photo" role="img" aria-label="Hands typing on a laptop keyboard" style="background:linear-gradient(135deg,#c9ccd0,#6b7178)"></div>
    <h3>Residential Alarm</h3><p>Mauris vel lacus vitae felis vestibulum volutpat imperdiet ac nisl Cum sociis natoque sodales velit</p>
  </div>
  <div class="feature abs" style="left:608px">
    <div class="photo" role="img" aria-label="Person in front of large digital screens" style="background:linear-gradient(135deg,#4f5d6c,#161c24)"></div>
    <h3>Cheap mms</h3><p>Mauris vel lacus vitae felis vestibulum volutpat imperdiet ac nisl Cum sociis natoque sodales velit</p>
  </div>
  <div class="feature abs" style="left:862px">
    <div class="photo" role="img" aria-label="Web hosting concept graphic" style="background:linear-gradient(135deg,#e6edf3,#6f8fb7)"></div>
    <h3>Web hosting</h3><p>Mauris vel lacus vitae felis vestibulum volutpat imperdiet ac nisl Cum sociis natoque sodales velit</p>
  </div>
  <svg class="curve" width="1200" height="60" viewBox="0 0 1200 60"><path d="M0 60 L0 30 Q600 -20 1200 30 L1200 60 Z" fill="#fff"/></svg>
</section>

<div class="subscribe-icon abs"><svg width="52" height="52" viewBox="0 0 52 52"><rect x="15" y="18" width="22" height="16" fill="none" stroke="#fff" stroke-width="2.5"/><path d="M15 18l11 9 11-9" fill="none" stroke="#fff" stroke-width="2.5"/></svg></div>
<div class="subscribe-text abs"><h3>Subscribe to our newsletter</h3><p>Stay up to date with the latest news.</p></div>
<div class="subscribe-form abs"><div class="field">Name</div><div class="btn">Subscribe</div></div>

<footer class="footer abs">
  <div class="brand abs"><span class="dot"></span>Prisvaktposten</div>
  <div class="socials abs"><span></span><span></span><span></span><span></span><span></span></div>
  <div class="col contact-col abs">
    <h4>Contact us</h4>
    <div class="addr">Prisvaktposten.no<br>48 Harbour Lane - Fjord Street<br>next to the Park</div>
    <div class="row"><svg width="16" height="16" viewBox="0 0 24 24"><path fill="#ddd" d="M6.6 10.8a15 15 0 0 0 6.6 6.6l2.2-2.2c.3-.3.7-.4 1-.2 1.1.4 2.3.6 3.6.6.6 0 1 .4 1 1V20c0 .6-.4 1-1 1A17 17 0 0 1 3 4c0-.6.4-1 1-1h3.5c.6 0 1 .4 1 1 0 1.3.2 2.5.6 3.6.1.3 0 .7-.2 1z"/></svg>Phone : 915-555-0182</div>
    <div class="row"><svg width="16" height="13" viewBox="0 0 26 20"><rect x="1" y="1" width="24" height="18" fill="none" stroke="#ddd" stroke-width="2"/><path d="M1 1l12 10L25 1" fill="none" stroke="#ddd" stroke-width="2"/></svg>Email : info@prisvaktposten.no</div>
  </div>
  <div class="col links-col abs">
    <h4>Quick links</h4>
    <ul><li>Home</li><li>About us</li><li>Contact</li><li>Terms</li><li>Privacy</li><li>Cookies</li></ul>
  </div>
  <div class="col news-col abs">
    <h4>Sign up for newsletter</h4>
    <p>Excepteur sint occaecat cupidatat non proident, sunt in culpa qui officia deserunt</p>
    <div class="field">Enter email</div>
    <span class="btn">Subscription</span>
  </div>
  <div class="bottom abs">©2017 Prisvaktposten.no, All Rights Reserved.</div>
</footer>

</body>
</html>
```